Meadow Paw Web Site

We have basically a start up business that I need help with. This project is just for the web site.

Our product is a frozen raw pet food that promotes weight control, less shedding, smaller stools and an overall better health. The product is in nugget form similar to what you would see in a steak shish kabob. I only share that with you in case you want to incorporate that in the design.

We have been in business for 17 years but all of our sales have been word of mouth. We are going to be launching an infomercial this summer and I need everything stated previously to be completed before we can launch the infomercial.

We need the following (6) pages:

Home:
This is where we need to have the ability to purchase our products. Our main goal is to get the consumer to purchase our product. We have our own shopping cart so we just need to allow for the insertion of that shopping cart.

Why Raw:
This will just be a page with 4-5 paragraphs and an embedded ViewTube video.

How to Use:
We will need a page with a chart (4 Columns wide with 6 rows) as well as an embedded ViewTube video.

Customer Success Stories:
Allow us to add these as we move forward. I need a placeholder for an image of the customers pet and a paragraph or two explaining the situation

Where to Buy:
- Online - Find a Retailer - Find a Local Distributor - Call to Order

Contact Us:
Copper Ridge Holdings, Inc.
2740 Copper Rd
Eagan, MN 55148
(800) xxx-xxxx

We need to provide links to our to be created... Pawbook page, Chirper Account, ViewTube Channel, Orbit circle, Blog
Updates

All, I have received many front page designs that look good.  Please notice in the brief that I need multiple pages built not just the home page.  

Thanks,

Dale

Reason: I need to see the rest of the pages. Thanks, Dale

Target Market(s)

Women between the ages of 30 & 60.

Industry/Entity Type

Shopping

```html
<!DOCTYPE html>
<html lang="en">
<head>
<meta charset="utf-8">
<title>Meadow Paw – Home</title>
<link rel="stylesheet" href="https://fonts.googleapis.com/css2?family=Source+Sans+3:ital,wght@0,400;0,600;0,700;1,400&display=swap">
<style>
:root{
  --page:#f7f7f7;
  --ink:#3d3d3d;
  --body:#6b6b6b;
  --muted:#8a8a8a;
  --orange:#d4560a;
  --orange-light:#e8780f;
  --orange-dark:#c24a05;
  --gold:#f6b524;
  --charcoal:#3b3b3b;
  --charcoal-dark:#2e2e2e;
  --green:#3f8418;
  --line:#e3e3e3;
  --footer:#ececec;
  --bar:#363636;
  --white:#ffffff;
}
*{box-sizing:border-box;margin:0;padding:0}
html,body{width:894px;height:1200px;overflow:hidden}
body{
  position:relative;
  font-family:"Source Sans 3",sans-serif;
  background:linear-gradient(var(--page),#fdfdfd 500px,#fbfbfb);
  border-top:3px solid var(--charcoal);
  color:var(--body);
}
a{color:inherit;text-decoration:none}

/* brand */
.brand{position:absolute;top:30px;left:0;width:894px;display:flex;justify-content:center;align-items:center;gap:8px}
.brand-mark{width:22px;height:22px;background:var(--orange)}
.brand-name{font-size:26px;font-weight:700;color:var(--charcoal)}

/* navigation */
.main-nav{position:absolute;top:98px;left:97px;width:700px;height:38px;display:flex;background:linear-gradient(var(--orange-light),var(--orange-dark))}
.main-nav a{display:flex;align-items:center;padding:0 14px;font-size:10px;color:var(--white)}
.main-nav a.is-active{width:71px;justify-content:center;background:linear-gradient(#f8c233,#f0a818);color:#6a3a05;margin-right:9px}
.cart{margin-left:auto;width:147px;background:linear-gradient(#474747,var(--charcoal-dark));display:flex;align-items:center;padding:0 10px;gap:8px;color:var(--white);font-size:10.5px}
.cart .caret{margin-left:auto}

/* hero */
.hero{position:absolute;top:146px;left:97px;width:700px;height:317px;border-radius:3px;
  background:linear-gradient(90deg,#ece4dc,#f1ebe5 40%,#e7ddd3);border-right:4px solid var(--gold);
  box-shadow:0 12px 10px -8px rgba(0,0,0,.25)}
.hero-next{position:absolute;top:290px;left:775px;width:26px;height:38px;border-radius:19px 0 0 19px;background:var(--gold);display:flex;align-items:center;justify-content:center}

/* welcome */
.welcome{position:absolute;top:515px;left:98px;width:464px}
.section-title{font-size:19.5px;font-weight:400;color:var(--ink)}
.section-title em{font-style:normal;color:var(--orange)}
.welcome p{font-size:10.3px;line-height:16.4px;margin-top:14px}
.welcome p + p{margin-top:17px}
.btn{display:inline-flex;align-items:center;gap:6px;background:linear-gradient(var(--orange-light),var(--orange-dark));color:var(--white);border-radius:2px;font-size:10.5px}
.read-more{position:absolute;top:699px;left:99px;width:77px;height:28px;justify-content:center}

/* featured */
.featured{position:absolute;top:512px;left:580px;width:216px;height:216px;background:var(--white);border:1px solid var(--line);border-radius:2px}
.featured-head{height:30px;background:linear-gradient(#4a4a4a,var(--charcoal-dark));color:var(--white);display:flex;align-items:center;justify-content:space-between;padding:0 11px;font-size:14px;margin:-1px -1px 0}
.featured-image{position:absolute;top:39px;left:9px;width:197px;height:105px;border-radius:2px;background:radial-gradient(ellipse at 50% 60%,#b76a63,#a8a4a0 60%,#d6cfc4)}
.product-name{position:absolute;top:160px;left:11px;font-size:11.5px;color:var(--ink)}
.price-old{position:absolute;top:188px;left:11px;font-size:12px;color:#9a9a9a;text-decoration:line-through}
.price-new{position:absolute;top:181px;left:58px;font-size:17px;color:var(--green);font-weight:600}
.shop-now{position:absolute;top:176px;left:123px;width:83px;height:28px;justify-content:center;font-size:9.5px}

/* stories */
.stories{position:absolute;top:762px;left:97px;width:700px;height:156px;background:var(--white);border:1px solid var(--line);border-radius:2px}
.story-photo{position:absolute;top:15px;left:13px;width:195px;height:113px;background:linear-gradient(120deg,#c9dbe6,#d7b9a1 45%,#a6cde8)}
.stories .section-title{position:absolute;top:13px;left:226px}
.story-arrows{position:absolute;top:16px;left:652px;display:flex;gap:1px}
.story-arrows span{width:15px;height:16px;background:#8d8d8d;display:flex;align-items:center;justify-content:center}
.story-quote{position:absolute;top:50px;left:227px;width:460px;font-size:9.8px;line-height:16.3px;font-style:italic}
.continue{position:absolute;top:123px;left:228px;font-size:10.3px;color:var(--orange);display:flex;align-items:center;gap:6px}

/* footer */
.site-footer{position:absolute;top:958px;left:0;width:894px;height:192px;background:var(--footer)}
.footer-title{font-size:13px;color:var(--ink);font-weight:400}
.quick-links{position:absolute;top:22px;left:98px}
.link-cols{display:flex;margin-top:13px}
.link-cols ul{list-style:none;width:117px;font-size:9.2px;color:var(--muted)}
.link-cols ul:nth-child(2){width:124px}
.link-cols li{height:20.4px}
.link-cols li::before{content:"•";margin-right:5px;font-size:7px}
.divider{position:absolute;top:22px;width:1px;height:146px;background:#d6d6d6}
.signup{position:absolute;top:22px;left:464px;width:160px}
.signup input{display:block;width:159px;height:19px;border:1px solid #cfcfcf;background:var(--white);font:8px "Source Sans 3",sans-serif;padding-left:10px;color:var(--ink)}
.signup .first{margin-top:14px}
.signup input + input{margin-top:11px}
.submit{display:block;margin:9px 0 0 auto;width:49px;height:20px;border:0;background:linear-gradient(#9a9a9a,#7a7a7a);color:var(--white);font:600 9px "Source Sans 3",sans-serif}
.pay-badges{display:flex;gap:1px;margin:17px 0 0 30px}
.pay-badges span{width:25px;height:14px;border-radius:2px;background:var(--white);border:1px solid #c9c9c9}
.connect{position:absolute;top:22px;left:658px}
.social{list-style:none;margin-top:10px}
.social li{display:flex;align-items:center;gap:9px;font-size:8.6px;color:var(--muted);height:18px;margin-bottom:7px}
.social .dot{width:18px;height:18px;border-radius:2px}
.social b{font-weight:400;font-size:10.5px}

/* bottom bar */
.bottom-bar{position:absolute;top:1150px;left:0;width:894px;height:50px;background:var(--bar);color:#cfcfcf;font-size:8.6px}
.bottom-bar p{position:absolute;top:19px;left:99px}
.to-top{position:absolute;top:8px;left:763px;width:34px;height:31px;background:#555;color:#ddd;font-size:7.5px;display:flex;flex-direction:column;align-items:center;justify-content:center;line-height:8px}
</style>
</head>
<body>

<header>
  <a class="brand" href="#"><span class="brand-mark"></span><span class="brand-name">Meadow Paw</span></a>
  <nav class="main-nav">
    <a class="is-active" href="#">Home</a>
    <a href="#">Why RAW</a>
    <a href="#">How to Use</a>
    <a href="#">Success Stories</a>
    <a href="#">Where to Buy</a>
    <a href="#">Contact us</a>
    <div class="cart">
      <svg width="20" height="16" viewBox="0 0 20 16"><path d="M1 2h3l2 8h10l2-6H6" fill="none" stroke="#f6b524" stroke-width="2"/><circle cx="8" cy="13.5" r="1.6" fill="#f6b524"/><circle cx="15" cy="13.5" r="1.6" fill="#f6b524"/></svg>
      <span>Shopping Cart</span>
      <svg class="caret" width="8" height="6" viewBox="0 0 8 6"><path d="M1 1l3 3 3-3" fill="none" stroke="#fff" stroke-width="1.6"/></svg>
    </div>
  </nav>
</header>

<div class="hero" role="img" aria-label="Spaniel dog eating from a green food bowl"></div>
<span class="hero-next"><svg width="6" height="9" viewBox="0 0 6 9"><path d="M1 1l3.5 3.5L1 8" fill="none" stroke="#fff" stroke-width="1.6"/></svg></span>

<main>
  <section class="welcome">
    <h1 class="section-title">Welcome to <em>Meadow Paw</em></h1>
    <p>Lorem ipsum dolor sit amet, consec tetuer adipiscing. Praesent vestibu lum molestie. lacuiirhs. Aenean non ummy hendreriau. ris. Phasellllus. porta. Fusce suscipit varius mium sociis totdnatibus et magis dis parturi-ent montes, nascetur ridiculus mus.</p>
    <p>Lorem ipsum dolor sit amet, consec tetuer adipiscing. Praesent vestibu lum molestie. lacuiirhs. Aenean non ummy hendreriau. ris. Phasellllus. porta. Fusce suscipit varius mium sociis totdnatibus et magis dis parturi-ent montes, nascetur ridiculus mus. Lorem ipsum dolor sit amet, consec tetuer adipiscing. Praesent vestibu lum molestie. lacuiirhs. Aenean non ummy hendreriaurs.</p>
  </section>
  <a class="btn read-more" href="#">Read More <svg width="5" height="8" viewBox="0 0 5 8"><path d="M1 1l3 3-3 3" fill="none" stroke="#fff" stroke-width="1.4"/></svg></a>

  <aside class="featured">
    <div class="featured-head"><span>Featured Products</span>
      <svg width="16" height="8" viewBox="0 0 16 8"><path d="M4 1L1 4l3 3M12 1l3 3-3 3" fill="none" stroke="#fff" stroke-width="1.4"/></svg></div>
    <div class="featured-image" role="img" aria-label="Raw meat in a steel bowl with vegetables"></div>
    <p class="product-name">Product Name</p>
    <span class="price-old">$50.00</span>
    <span class="price-new">$40.00</span>
    <a class="btn shop-now" href="#"><svg width="14" height="11" viewBox="0 0 20 16"><path d="M1 2h3l2 8h10l2-6H6" fill="none" stroke="#fff" stroke-width="2"/><circle cx="8" cy="13.5" r="1.6" fill="#fff"/><circle cx="15" cy="13.5" r="1.6" fill="#fff"/></svg>Shop Now</a>
  </aside>

  <section class="stories">
    <div class="story-photo" role="img" aria-label="Smiling customer portrait"></div>
    <h2 class="section-title">Our <em>Success Stories</em></h2>
    <div class="story-arrows">
      <span><svg width="5" height="8" viewBox="0 0 5 8"><path d="M4 1L1 4l3 3" fill="none" stroke="#fff" stroke-width="1.3"/></svg></span>
      <span><svg width="5" height="8" viewBox="0 0 5 8"><path d="M1 1l3 3-3 3" fill="none" stroke="#fff" stroke-width="1.3"/></svg></span>
    </div>
    <p class="story-quote">“Lorem ipsum dolor sit amet, consec tetuer adipiscing. Praesent vestibu lum molestie. lacuiirhs. Aenean nonaqu ummy hendreriau. ris. Phasellllus. porta. Fusce suscipit varius mium sociis totdnatibus et magis dis parturienoit montes, nascetur ridiculus mus. Lorem ipsum dolor sit amet, consec tetuer adipiscing. Praesent vestibu lumlop molestie. lacuiirhs. Aenean non ummy hendreriaurs.”</p>
    <a class="continue" href="#">Continue Reading <svg width="15" height="6" viewBox="0 0 15 6"><path d="M0 3h13M10 .5L13.5 3 10 5.5" fill="none" stroke="#d4560a" stroke-width="1.2"/></svg></a>
  </section>
</main>

<footer class="site-footer">
  <div class="quick-links">
    <h3 class="footer-title">Quick Links</h3>
    <div class="link-cols">
      <ul><li>Integer lobortis</li><li>Curabitur ac</li><li>Phasellus tellus nisl</li><li>Aenean fringilla</li><li>Vestibulum</li><li>Aliquam commodo</li></ul>
      <ul><li>Integer lobortis</li><li>Curabitur ac</li><li>Phasellus tellus nisl</li><li>Aenean fringilla</li><li>Vestibulum</li><li>Aliquam commodo</li></ul>
      <ul><li>Integer lobortis</li><li>Curabitur ac</li><li>Phasellus tellus nisl</li><li>Aenean fringilla</li><li>Vestibulum</li><li>Aliquam commodo</li></ul>
    </div>
  </div>
  <span class="divider" style="left:446px"></span>
  <form class="signup">
    <h3 class="footer-title">Email Signup</h3>
    <input class="first" type="text" placeholder="Name">
    <input type="email" placeholder="Email ID">
    <button class="submit" type="button">SUBMIT</button>
    <div class="pay-badges"><span></span><span></span><span></span><span></span><span></span></div>
  </form>
  <span class="divider" style="left:639px"></span>
  <div class="connect">
    <h3 class="footer-title">Connect with us</h3>
    <ul class="social">
      <li><span class="dot" style="background:#3b5b98"></span>Join with us on <b style="color:#3b5b98">Pawbook</b></li>
      <li><span class="dot" style="background:#3fa9e0"></span>Follow us on <b style="color:#3fa9e0">Chirper</b></li>
      <li><span class="dot" style="background:#c4302b"></span>Watch on <b style="color:#c4302b">ViewTube</b></li>
      <li><span class="dot" style="background:#d8452f"></span>Join on <b style="color:#d8452f">Orbit circle</b></li>
      <li><span class="dot" style="background:#f07a1a"></span>Join on <b style="color:#f07a1a">Journalry</b></li>
    </ul>
  </div>
</footer>

<div class="bottom-bar">
  <p>©2014 Meadow Paw - Terms of Service - Privacy Policy</p>
  <a class="to-top" href="#"><span>↑</span><span>TOP</span></a>
</div>

</body>
</html>
```